BOLD & MINIMALIST DESIGN NEEDED

We want a very bold but minimalistic business card design that is impactful and utilizes both sides of the business card. Our current logo is included for your use.

We want bold fonts and good use of negative space. We don't want the logo to overpower the design.

Target Market(s)

Professionals who are building new commercial buildings.

Industry/Entity Type

Construction

Contact Information for Business Card

Name, Title, email, office phone, cell phone, website

Font styles to use
Serif
Sans Serif

Requirements
Must have
• Bold design!

```html
<!DOCTYPE html>
<html lang="en">
<head>
<meta charset="UTF-8">
<title>Ridgeline Build — Business Card</title>
<link href="https://fonts.googleapis.com/css2?family=Poppins:wght@300;400;500;800&display=swap" rel="stylesheet">
<style>
  :root {
    --stage: #2a2a2c;
    --ink: #0c0c0e;
    --paper: #ffffff;
    --green: #7dc242;
    --white: #ffffff;
  }
  * { box-sizing: border-box; margin: 0; padding: 0; }
  html, body {
    width: 1200px; height: 1200px; overflow: hidden;
    background: var(--stage);
    font-family: "Poppins", sans-serif;
  }
  .canvas {
    position: relative; width: 1200px; height: 1200px;
  }
  .card {
    position: absolute; left: 150px; width: 900px; height: 500px;
    overflow: hidden;
  }
  /* Back side */
  .card-back {
    top: 55px; background: var(--ink); color: var(--white);
    display: flex; flex-direction: column; align-items: center; justify-content: center;
  }
  .brand-lockup {
    display: flex; align-items: center; gap: 22px;
  }
  .brand-square {
    width: 46px; height: 46px; background: var(--green);
  }
  .brand-name-back {
    font-weight: 800; font-size: 76px; letter-spacing: 1px; line-height: 1;
    color: var(--white);
  }
  .back-website {
    margin-top: 44px; font-weight: 400; font-size: 26px; letter-spacing: 9px;
    color: var(--white);
  }
  /* Front side */
  .card-front {
    top: 645px; background: var(--paper); color: var(--ink);
  }
  .brand-name-front {
    position: absolute; left: 0; right: 0; top: 58px; text-align: center;
    font-weight: 800; font-size: 104px; line-height: 1; letter-spacing: 1px;
    color: var(--ink);
  }
  .brand-rule {
    position: absolute; left: 150px; right: 150px; top: 178px; height: 3px; background: var(--ink);
  }
  .person {
    position: absolute; left: 80px; top: 240px; width: 290px; text-align: right;
  }
  .person-name {
    font-weight: 800; font-size: 34px; line-height: 1.1; letter-spacing: 0.5px;
  }
  .person-title {
    font-weight: 300; font-size: 22px; letter-spacing: 3px; color: var(--green);
  }
  .divider {
    position: absolute; left: 400px; top: 235px; width: 4px; height: 110px; background: var(--green);
  }
  .contacts {
    position: absolute; left: 430px; top: 236px; list-style: none;
  }
  .contact-item {
    display: flex; align-items: center; gap: 14px;
    font-size: 25px; font-weight: 400; line-height: 36px; color: var(--ink);
  }
  .contact-icon { width: 26px; height: 26px; flex: none; }
  .address-band {
    position: absolute; left: 0; right: 0; top: 378px; height: 66px;
    background: var(--green); display: flex; align-items: center; justify-content: center;
    font-size: 26px; font-weight: 400; color: var(--ink);
  }
</style>
</head>
<body>
<main class="canvas">
  <section class="card card-back" aria-label="Card back">
    <div class="brand-lockup">
      <span class="brand-square"></span>
      <span class="brand-name-back">RIDGELINE BUILD</span>
    </div>
    <p class="back-website">www.ridgelinebuild.com</p>
  </section>

  <section class="card card-front" aria-label="Card front">
    <h1 class="brand-name-front">RIDGELINE BUILD</h1>
    <div class="brand-rule"></div>

    <div class="person">
      <p class="person-name">DANIEL BROOKS</p>
      <p class="person-title">MANAGER</p>
    </div>

    <div class="divider"></div>

    <ul class="contacts">
      <li class="contact-item">
        <svg class="contact-icon" viewBox="0 0 26 26" aria-hidden="true">
          <circle cx="13" cy="13" r="13" fill="var(--green)"/>
          <path d="M9 7c1 0 2 2 2 3s-1 1-1 2 2 3 3 3 1-1 2-1 3 1 3 2-1 2-2 2c-4 0-9-5-9-9 0-1 1-2 2-2z" fill="#fff"/>
        </svg>
        (555) 218-4076
      </li>
      <li class="contact-item">
        <svg class="contact-icon" viewBox="0 0 26 26" aria-hidden="true">
          <circle cx="13" cy="13" r="13" fill="var(--green)"/>
          <rect x="6.5" y="8.5" width="13" height="9" fill="none" stroke="#fff" stroke-width="1.5"/>
          <path d="M6.5 8.5 13 13.5 19.5 8.5" fill="none" stroke="#fff" stroke-width="1.5"/>
        </svg>
        hello@ridgelinebuild.com
      </li>
      <li class="contact-item">
        <svg class="contact-icon" viewBox="0 0 26 26" aria-hidden="true">
          <circle cx="13" cy="13" r="13" fill="var(--green)"/>
          <circle cx="13" cy="13" r="7" fill="none" stroke="#fff" stroke-width="1.4"/>
          <ellipse cx="13" cy="13" rx="3" ry="7" fill="none" stroke="#fff" stroke-width="1.2"/>
          <path d="M6 13h14M7.5 9.5h11M7.5 16.5h11" stroke="#fff" stroke-width="1.1"/>
        </svg>
        www.ridgelinebuild.com
      </li>
    </ul>

    <p class="address-band">PO BOX 48 Harbour Lane, 3rd street Geelong</p>
  </section>
</main>
</body>
</html>
```